Make it cool to work near where you are...

Calling all creatives - create the ultimate cool card for people who want to cut their commute.

Here at PineNook we've got what can best be described as an Flintpass card for desks - and we want to brighten up the wallets of our most loyal users.

So, pitch us your ideas and you might see your design on cards being flashed across the country - and we've thrown in a bit of cash too.

Do see our brief card guidelines - with a couple of past examples thrown in.

```html
<!DOCTYPE html>
<html lang="en">
<head>
<meta charset="utf-8">
<title>PineNook business card</title>
<link href="https://fonts.googleapis.com/css2?family=Lato:wght@400;700;900&display=swap" rel="stylesheet">
<style>
  :root {
    --backdrop: #e9e6e1;
    --charcoal: #2b2b2d;
    --charcoal-light: #4a4a4d;
    --graphite: #5b5b5e;
    --paper: #ffffff;
    --paper-shade: #ececec;
    --magenta: #e2268f;
    --ink: #3a3a3c;
    --soft-text: #e4e4e4;
  }
  * { box-sizing: border-box; margin: 0; padding: 0; }
  html, body { width: 1200px; height: 900px; overflow: hidden; }
  body {
    background: var(--backdrop);
    font-family: "Lato", Arial, sans-serif;
    position: relative;
  }
  .card {
    position: absolute;
    left: 260px;
    width: 680px;
    height: 390px;
    border-radius: 24px;
    overflow: hidden;
    box-shadow: 0 10px 28px rgba(0,0,0,.22);
  }
  /* front */
  .card-front {
    top: 40px;
    background: radial-gradient(ellipse at 45% 35%, var(--charcoal-light) 0%, var(--charcoal) 70%);
  }
  .front-wordmark {
    position: absolute;
    top: 130px;
    left: 0; right: 0;
    display: flex;
    justify-content: center;
    align-items: center;
    gap: 18px;
  }
  .front-wordmark .mark-square {
    width: 34px; height: 34px;
    background: var(--magenta);
  }
  .front-wordmark .name {
    font-weight: 900;
    font-size: 84px;
    letter-spacing: -2px;
    color: var(--paper);
    line-height: 1;
  }
  .front-url {
    position: absolute;
    bottom: 56px;
    left: 0; right: 0;
    text-align: center;
    color: var(--soft-text);
    font-weight: 700;
    font-size: 20px;
  }
  /* back */
  .card-back {
    top: 470px;
    background: linear-gradient(160deg, var(--paper) 40%, var(--paper-shade) 100%);
  }
  .card-back svg.sweep { position: absolute; inset: 0; }
  .back-wordmark {
    position: absolute;
    left: 46px; top: 122px;
    display: flex; align-items: center; gap: 10px;
  }
  .back-wordmark .mark-square {
    width: 14px; height: 14px; background: var(--magenta);
  }
  .back-wordmark .name {
    font-weight: 900; font-size: 40px; letter-spacing: -1px;
    color: var(--ink); line-height: 1;
  }
  .person { position: absolute; left: 46px; top: 225px; }
  .person .person-name { color: var(--magenta); font-weight: 700; font-size: 20px; }
  .person .person-role { color: var(--ink); font-size: 15px; margin-top: 2px; }
  .contacts {
    position: absolute; right: 30px; top: 200px;
    list-style: none; color: var(--soft-text); font-size: 14px;
  }
  .contacts li { display: flex; align-items: center; gap: 8px; margin-bottom: 6px; }
  .contacts svg { width: 16px; height: 16px; flex: none; }
  .address {
    position: absolute; right: 150px; bottom: 36px;
    color: var(--soft-text); font-size: 14px; line-height: 1.45;
  }
</style>
</head>
<body>

<section class="card card-front">
  <div class="front-wordmark">
    <span class="mark-square"></span>
    <span class="name">PineNook</span>
  </div>
  <p class="front-url">www.pinenook.com</p>
</section>

<section class="card card-back">
  <svg class="sweep" viewBox="0 0 680 390" preserveAspectRatio="none" aria-hidden="true">
    <defs>
      <linearGradient id="darkPanel" x1="0" y1="0" x2="1" y2="1">
        <stop offset="0" stop-color="#5e5e61"/>
        <stop offset="1" stop-color="#2e2e30"/>
      </linearGradient>
    </defs>
    <path d="M 588 0 C 520 190, 260 330, 0 352" fill="none" stroke="#e2268f" stroke-width="9"/>
    <path d="M 612 0 C 540 200, 280 345, 0 372 L 0 390 L 680 390 L 680 0 Z" fill="url(#darkPanel)"/>
    <path d="M 0 378 L 680 378" stroke="#e2268f" stroke-width="0"/>
    <rect x="0" y="380" width="680" height="10" fill="#e2268f"/>
  </svg>

  <div class="back-wordmark">
    <span class="mark-square"></span>
    <span class="name">PineNook</span>
  </div>

  <div class="person">
    <p class="person-name">Sam Rowe</p>
    <p class="person-role">Managing Director</p>
  </div>

  <ul class="contacts">
    <li>
      <svg viewBox="0 0 16 16"><path d="M4 2 L6.5 5 L5 6.5 C6 8.5 7.5 10 9.5 11 L11 9.5 L14 12 L12.5 14 C7 13.5 2.5 9 2 3.5 Z" fill="#e4e4e4"/></svg>
      +44 20 7946 0321
    </li>
    <li>
      <svg viewBox="0 0 16 16"><rect x="1.5" y="3.5" width="13" height="9" fill="none" stroke="#e4e4e4" stroke-width="1.4"/><path d="M1.5 3.5 L8 9 L14.5 3.5" fill="none" stroke="#e4e4e4" stroke-width="1.4"/></svg>
      team@pinenook.com
    </li>
    <li>
      <svg viewBox="0 0 16 16"><circle cx="8" cy="8" r="6.3" fill="none" stroke="#e4e4e4" stroke-width="1.3"/><ellipse cx="8" cy="8" rx="2.8" ry="6.3" fill="none" stroke="#e4e4e4" stroke-width="1.1"/><path d="M1.7 8 H14.3" stroke="#e4e4e4" stroke-width="1.1"/></svg>
      www.pinenook.com
    </li>
  </ul>

  <p class="address">NookHouse, 48 Alder Street<br>E2 7QP London, United Kingdom</p>
</section>

</body>
</html>
```